Brochure Design Project - Glass Cabinets

We are a small but rapidly expanding company providing glass display furniture to retailers and other organisations to display their product. We specialise in all-glass, frameless display cabinets and showcases. Our products include glass cabinets, wall units, shelving units, etc. Our main market was initially householders, then retailers, but has increasingly become corporates who want to display their corporate prizes/trophies, and are also fit-out companies who have discovered our products and are interested in them. We want to make the most of this development, and we want this brochure to help us.
We have identified shop fit-out companies and fit-out designers as a target market for the coming year, so we need some literature that will introduce our company to these businesses, and encourage them to use our products in their designs.
This brochure will not be a product catalogue (we already have that), but a corporate profile that introduces our company and its services. We need to communicate the message that we are a serious provider of good quality glass display furniture, and that we stand for innovation, value, and good design.
We will be giving these brochures out when we make marketing approaches to the shop fit-out companies.
We envisage that the brochure will be a one A4 page brochure, with the back side used for examples of our work. We are open to suggestions about this, however. For example, it could conceivably be DLE format.
We expect some of the copy will be in text boxes. We will upload further details of the examples on page 2 in the next few days.
It needs to be full colour.
It will be offset printed.
The output needs to be PC compatible, preferably produced in Indesign so it is compatible with our software.
Please see our website and other uploaded files for examples of our current imagery. The corporate brochure needn't follow this slavishly, but should be cognizant of it.

Reason: The deadline has been extended because there is some further information I will put up, regarding page two. Also, I will spend some time providing feedback.

Thank you to all who have submitted designs for my project. They are all very much appreciated. I have responded to most of you, but some general comments that come to mind are that the brochure needs to 1) appeal to the emotions more i.e. be more evocative of sophistication. This means not necessarily using just the images I have uploaded, but maybe suggest design elements that are more creative than 'blocky', and 2) be designed to sell the company rather than its products. This is partly my fault, I think, although it is a learning experience for me also. In general I think there is too much information to include, especially copy but also images, forcing designers to make the designs quite boring in order to accommodate it. I intend to cut the information significantly and will repost. Having said that, I am trying to see through the overload of information and look for designs that include elements that are creative and sophisticated. Sometimes less is more. Apologies if I am confusing you, but the main thing is to make the brochure appeal to the emotions i.e. 'this company is sophisticated and and be depended upon', and less to the products themselves. I welcome any questions you may have.

Thanks to all the designers who have submitted designs. There are some great ideas coming through now, and on the basis of these ideas I have been able to determine what the brochure needs to look like much more precisely. Some of the designs have been too crowded, because there has been too much information to include. I have therefore decided that the brochure needs to be a 4 page A4 brochure (A3 folded in half). I have altered the copy in the Word document to reflect this. The middle spread is now dedicated to jobs previously done, and includes logos of other high profile customers. The front page can now be dedicated to providing very basic, introductory information and an eye-catching graphic, while the back page has further detail about the company and contact details. To reflect the fact that this will involve some redesign work, I have increased the budget. I have also extended the deadline by a week. I thank you for your patience, but sometimes a design project is iterative. Please see the newly uploaded files.

Reason: Thanks to all the designers who have submitted designs. There are some great ideas coming through now, and on the basis of these ideas I have been able to determine what the brochure needs to look like much more precisely. Some of the designs have been too crowded, because there has been too much information to include. I have therefore decided that the brochure needs to be a 4 page A4 brochure (A3 folded in half). I have altered the copy in the Word document to reflect this. The middle spread is now dedicated to jobs previously done, and includes logos of other high profile customers. The front page can now be dedicated to providing very basic, introductory information and an eye-catching graphic, while the back page has further detail about the company and contact details. To reflect the fact that this will involve some redesign work, I have increased the budget. I have also extended the deadline by a week. I thank you for your patience, but sometimes a design project is iterative. Please see the newly uploaded files.

Target Market(s)

Shop Fit-out companies, Fit-out designers, Retailers

Industry/Entity Type

Marketing

Requirements
Must have
• Existing logo
Full colour, with overprint

```html
<!DOCTYPE html>
<html lang="en">
<head>
<meta charset="utf-8">
<title>Clearform Glass – Brochure</title>
<link href="https://fonts.googleapis.com/css2?family=Ubuntu:wght@300;400;500&display=swap" rel="stylesheet">
<style>
  :root{
    --stage:#1f2326;
    --plum:#4e3150;
    --lime:#a2bd4e;
    --lime-soft:#c3d68a;
    --label:#9bb84e;
    --white:#ffffff;
    --ink:#2b2430;
  }
  *{margin:0;padding:0;box-sizing:border-box}
  html,body{width:1200px;height:1000px;overflow:hidden;background:var(--stage);font-family:"Ubuntu",sans-serif}
  .canvas{position:relative;width:1200px;height:1000px}
  .page-label{position:absolute;top:50px;width:200px;text-align:center;color:var(--label);font-size:23px;font-weight:400}
  .page{position:absolute;top:97px;width:565px;height:800px;overflow:hidden}
  .page--front{left:22px;background:var(--plum)}
  .page--back{left:610px;background:var(--lime)}
  .page svg.art{position:absolute;left:0;top:0;width:565px;height:800px}

  .brand{position:absolute;left:24px;top:24px;display:flex;align-items:center;gap:12px;color:var(--lime-soft)}
  .brand-mark{width:36px;height:36px;background:var(--lime-soft)}
  .brand-name{font-size:26px;font-weight:400;letter-spacing:.5px;line-height:1}
  .brand-tag{font-size:16px;font-weight:300;margin-top:4px;line-height:1}

  .headline{position:absolute;left:88px;top:354px;color:var(--white);font-size:22.5px;font-weight:300;letter-spacing:1.6px;white-space:nowrap}
  .intro{position:absolute;top:398px;color:var(--white);font-size:9px;line-height:1.3}
  .intro p{margin-bottom:11px}
  .intro--left{left:88px;width:180px;text-align:justify}
  .intro--right{left:282px;width:178px}
  .contact{position:absolute;left:88px;top:692px;color:var(--white);font-size:11.5px;line-height:1.35}
  .contact .lead{margin-bottom:3px;color:#2f2433}

  .copy{position:absolute;top:16px;color:var(--white);font-size:9px;line-height:1.27}
  .copy--left{left:32px;width:232px}
  .copy--right{left:290px;width:246px}
  .copy h3{font-size:9px;font-weight:400}
  .copy ul{list-style:disc;padding-left:17px}
  .copy p{margin-bottom:11px}
  .caption{font-size:6.8px;font-weight:500;fill:#2a2a2a;font-family:"Ubuntu",sans-serif}
  .clients{position:absolute;top:672px;color:var(--ink);font-size:7.2px;font-weight:500;line-height:1.28}
  .clients--left{left:211px}
  .clients--right{left:354px;top:682px}
</style>
</head>
<body>
<div class="canvas">
  <div class="page-label" style="left:198px">1 page</div>
  <div class="page-label" style="left:792px">2 page</div>

  <!-- Front page -->
  <section class="page page--front">
    <svg class="art" viewBox="0 0 565 800">
      <defs>
        <linearGradient id="heroTone" x1="0" y1="0.15" x2="1" y2="0.85">
          <stop offset="0" stop-color="#e9cfa6"/>
          <stop offset=".14" stop-color="#c98a5e"/>
          <stop offset=".3" stop-color="#5a84b8"/>
          <stop offset=".45" stop-color="#3f6e9f"/>
          <stop offset=".58" stop-color="#7fb9c6"/>
          <stop offset=".72" stop-color="#b6dde2"/>
          <stop offset=".86" stop-color="#c9a0b4"/>
          <stop offset="1" stop-color="#d58fa3"/>
        </linearGradient>
        <linearGradient id="textShade" x1="0" y1="0" x2="0" y2="1">
          <stop offset="0" stop-color="#1a2a40" stop-opacity="0"/>
          <stop offset=".45" stop-color="#1a2a40" stop-opacity=".28"/>
          <stop offset=".7" stop-color="#1a2a40" stop-opacity=".12"/>
          <stop offset="1" stop-color="#1a2a40" stop-opacity=".3"/>
        </linearGradient>
      </defs>
      <polygon points="0,133 565,18 565,800 0,800" fill="url(#heroTone)" role="img" aria-label="Photo of a young couple leaning over a glass display cabinet in a shop, pointing at the items inside"/>
      <polygon points="0,133 565,18 565,800 0,800" fill="url(#textShade)" aria-hidden="true"/>
    </svg>
    <div class="brand">
      <div class="brand-mark"></div>
      <div>
        <div class="brand-name">CLEARFORM GLASS</div>
        <div class="brand-tag">design strength value</div>
      </div>
    </div>
    <h1 class="headline">UNIQUE - INNOVATIVE - CREATIVE</h1>
    <div class="intro intro--left">
      <p>Clearform Glass is one of New Zealand's leading suppliers of high quality showcases, display cases and display cabinets.</p>
      <p>We specialise in all-glass display cabinets that minimise visual obstructions to the cabinet's contents.</p>
      <p>Our range is unique, our service is exceptional, our attention to detail will surprise you.</p>
    </div>
    <div class="intro intro--right">
      <p>Glass is timeless, and always fashionable. Whatever your situation, a quality glass cabinet from Clearform Glass will serve you well.</p>
      <p>Ideal for businesses, residential, schools, organisations.</p>
    </div>
    <div class="contact">
      <div class="lead">Contact us now to discuss your requirements.</div>
      <div>Martin Harlow (Director)</div>
      <div>Ph. 021 555 0148</div>
      <div>Fax (09) 555 0172</div>
      <div>Email: martin@clearformglass.example</div>
      <div>Website: www.clearformglass.example</div>
    </div>
  </section>

  <!-- Back page -->
  <section class="page page--back">
    <svg class="art" viewBox="0 0 565 800">
      <defs>
        <linearGradient id="shopWarm" x1="0" y1="0" x2="1" y2="1"><stop offset="0" stop-color="#c9b59a"/><stop offset="1" stop-color="#8c7a66"/></linearGradient>
        <linearGradient id="shopCool" x1="0" y1="0" x2="1" y2="1"><stop offset="0" stop-color="#d9d6cf"/><stop offset="1" stop-color="#a09c94"/></linearGradient>
        <linearGradient id="shopBold" x1="0" y1="0" x2="1" y2="1"><stop offset="0" stop-color="#5f6f9a"/><stop offset="1" stop-color="#c9a46a"/></linearGradient>
        <linearGradient id="shopOrange" x1="0" y1="0" x2="1" y2="1"><stop offset="0" stop-color="#d89a62"/><stop offset="1" stop-color="#9a8d80"/></linearGradient>
      </defs>
      <polygon fill="var(--plum)" points="0,335 195,210 360,258 565,218 565,713 380,590 0,710"/>
      <polygon fill="var(--lime)" points="0,352 565,232 565,240 0,360"/>
      <g role="img" aria-label="Photos of completed shop fit-outs with glass cabinets">
        <polygon fill="url(#shopWarm)" points="0,362 188,322 188,468 0,505"/>
        <polygon fill="url(#shopCool)" points="190,322 385,280 385,427 190,468"/>
        <polygon fill="url(#shopBold)" points="387,280 565,242 565,372 387,427"/>
      </g>
      <polygon fill="var(--lime)" points="0,505 565,374 565,384 0,515"/>
      <g role="img" aria-label="Photos of glass display cabinets in client premises">
        <polygon fill="url(#shopCool)" points="0,517 188,473 188,640 0,675"/>
        <polygon fill="url(#shopOrange)" points="190,472 385,430 385,596 190,640"/>
        <polygon fill="url(#shopCool)" points="387,429 565,386 565,508 387,552"/>
      </g>
      <polygon fill="var(--lime)" points="0,675 565,500 565,508 0,683"/>
      <text class="caption" x="10" y="483">Marlowe Jewellery</text>
      <text class="caption" x="198" y="438">Quadrant Tech</text>
      <text class="caption" x="392" y="387">Hillcrest Foods</text>
      <text class="caption" x="10" y="642">Whitcombe's</text>
      <text class="caption" x="198" y="582">Tasman Naval Club</text>
      <text class="caption" x="392" y="520">Lighthouse Mission</text>
    </svg>
    <div class="copy copy--left">
      <h3>Clearform Glass:</h3>
      <ul>
        <li>Anything from a single unit to a whole shop.</li>
        <li>A design service for your shop-fitout needs.</li>
        <li>Frameless, framed, or UV bonded cabinets.</li>
        <li>All glass toughened.</li>
        <li>We supply custom build cabinets and also have a standard range we keep in stock.</li>
        <li>New Zealand's largest range of frameless cabinets.</li>
        <li>Exceptional prices for very high quality cabinets.</li>
        <li>Cabinet options include LED lights, cupboards, mirrors, wheels, extra clear glass, etc.</li>
        <li>We guarantee delivery of unbroken cabinets.</li>
      </ul>
    </div>
    <div class="copy copy--right">
      <h3>Service</h3>
      <p>We believe in providing customers with well-designed, high quality products at a great price. Our standard range is kept in stock, so we can supply immediately.</p>
      <h3>Value</h3>
      <p>All glass and components are of the highest quality.</p>
      <h3>Range</h3>
      <p>As well as New Zealand's largest range of frameless glass cabinets, we also stock a range of framed cabinets, counters, free-standing shelving units, wall units, and kiosk counters.<br>Custom made cabinets can be a single unit to a shop lot.</p>
      <h3>Strength</h3>
      <p>All glass is 6.1mm or 7.1mm toughened glass.</p>
    </div>
    <div class="clients clients--left">
      <div>A selection of our customers:</div>
      <div>Harbourline Builders</div><div>Brightwater Drinks</div><div>Kestrel Power</div>
      <div>Tasman Naval Club</div><div>Northgate University</div><div>Quadrant Tech</div>
      <div>Harbour Lights Casino</div><div>Whitcombe's Dunmore</div><div>Pacific Pension Trust</div>
      <div>Ferndale Furnishings Riverton</div><div>Vision Aid Society</div>
    </div>
    <div class="clients clients--right">
      <div>Redline Ambulance Trust</div><div>Lighthouse Mission</div><div>Toolbox Hardware</div>
      <div>Crossway Car Services</div><div>Hillcrest Foods</div><div>Kowhai Bay College</div>
      <div>Eastbrook College</div>
    </div>
  </section>
</div>
</body>
</html>
```